VOMRA Pty Ltd Business Card

Looking for a simple yet eye-catching double-sided business card design using my company logo on one side and contact details on the other.

Target Market(s)

Government

Industry/Entity Type

Communication Systems Engineering

Contact Information for Business Card

VOMRA Pty Ltd

Requirements
Nice to have
• Would be great to have a QR code so details can be scanned into contacts

```html
<!DOCTYPE html>
<html lang="en">
<head>
<meta charset="utf-8">
<title>VOMRA Pty Ltd Business Card</title>
<link href="https://fonts.googleapis.com/css2?family=Montserrat:wght@400;700&display=swap" rel="stylesheet">
<style>
  :root {
    --bg: #dcdcd9;
    --card: #ffffff;
    --slate: #3a434b;
    --ink: #000000;
    --text: #3a434b;
  }
  * { margin: 0; padding: 0; box-sizing: border-box; }
  html, body { width: 1200px; height: 801px; overflow: hidden; }
  body {
    background: var(--bg);
    font-family: "Montserrat", Arial, sans-serif;
    color: var(--text);
    position: relative;
  }
  .card {
    position: absolute;
    width: 560px;
    height: 320px;
    background: var(--card);
    border-radius: 18px;
    overflow: hidden;
    box-shadow: 0 6px 18px rgba(0,0,0,0.18);
  }
  .card--front { left: 20px; top: 240px; }
  .card--back { left: 620px; top: 240px; }

  .swoosh { position: absolute; inset: 0; width: 100%; height: 100%; }
  .swoosh .band-outer { fill: var(--slate); }
  .swoosh .band-gap { fill: var(--card); }
  .swoosh .band-black { fill: var(--ink); }
  .swoosh .band-fill { fill: var(--slate); }

  .brand {
    position: absolute;
    display: flex;
    align-items: center;
    gap: 10px;
    font-weight: 700;
    color: var(--slate);
    letter-spacing: 1px;
  }
  .brand__dot { border-radius: 50%; background: var(--slate); }
  .card--front .brand { left: 30px; top: 122px; font-size: 42px; }
  .card--front .brand__dot { width: 18px; height: 18px; }
  .card--back .brand { left: 50%; top: 50%; transform: translate(-50%, -50%); font-size: 84px; }
  .card--back .brand__dot { width: 34px; height: 34px; }

  .divider {
    position: absolute;
    left: 268px; top: 48px;
    width: 1.5px; height: 160px;
    background: var(--slate);
  }
  .contact { position: absolute; left: 286px; top: 38px; }
  .contact__name { font-weight: 700; font-size: 18px; letter-spacing: 0.5px; line-height: 1.1; }
  .contact__role { font-size: 12px; margin-top: 2px; }
  .contact__list { list-style: none; margin-top: 12px; font-size: 12px; line-height: 1.5; }
  .contact__list li { display: flex; align-items: center; gap: 7px; }
  .contact__list svg { width: 10px; height: 10px; fill: var(--slate); }
  .contact__address { margin-top: 10px; font-size: 12px; line-height: 1.4; }
</style>
</head>
<body>
  <section class="card card--front" aria-label="Business card, contact side">
    <svg class="swoosh" viewBox="0 0 560 320" preserveAspectRatio="none" aria-hidden="true">
      <path class="band-outer" d="M0,228 C170,300 360,250 560,222 L560,320 L0,320 Z"/>
      <path class="band-gap" d="M0,232 C170,304 362,254 560,226 L560,320 L0,320 Z"/>
      <path class="band-black" d="M0,236 C170,308 364,258 560,230 L560,320 L0,320 Z"/>
      <path class="band-gap" d="M0,248 C172,318 368,268 560,242 L560,320 L0,320 Z"/>
      <path class="band-fill" d="M0,254 C174,324 370,272 560,247 L560,320 L0,320 Z"/>
    </svg>

    <div class="brand"><span class="brand__dot"></span><span class="brand__name">VOMRA</span></div>

    <div class="divider"></div>

    <div class="contact">
      <p class="contact__name">DECLAN HARWOOD</p>
      <p class="contact__role">Managing Director</p>
      <ul class="contact__list">
        <li><svg viewBox="0 0 24 24"><path d="M6.6 10.8a15 15 0 0 0 6.6 6.6l2.2-2.2a1 1 0 0 1 1-.25 11.4 11.4 0 0 0 3.6.57 1 1 0 0 1 1 1V20a1 1 0 0 1-1 1A17 17 0 0 1 3 4a1 1 0 0 1 1-1h3.5a1 1 0 0 1 1 1c0 1.25.2 2.45.57 3.57a1 1 0 0 1-.25 1z"/></svg>135 792 468</li>
        <li><svg viewBox="0 0 24 24"><path d="M2 5h20v14H2z M2 5l10 8 10-8"/></svg>admin@vomra.com.au</li>
        <li><svg viewBox="0 0 24 24"><circle cx="12" cy="12" r="10"/></svg>www.vomra.com.au</li>
      </ul>
      <p class="contact__address">14 Larkin Lane Brookvale<br>NSW 2100 Australia</p>
    </div>
  </section>

  <section class="card card--back" aria-label="Business card, brand side">
    <div class="brand"><span class="brand__dot"></span><span class="brand__name">VOMRA</span></div>
  </section>
</body>
</html>
```